Education Certificate

We need a modern yet professional Certificate for those who successfully pass / complete our online Training course.

There are various courses but ONE certificate design required.

the certificate needs to look extremely professional and of value.

```html
<!DOCTYPE html>
<html lang="en">
<head>
<meta charset="utf-8">
<title>Certificate of Completion</title>
<link rel="stylesheet" href="https://fonts.googleapis.com/css2?family=Montserrat:wght@600;700;900&family=Poppins:wght@400;500&family=Mrs+Saint+Delafield&display=swap">
<style>
  :root {
    --page: #d8d9e1;
    --paper: #ffffff;
    --navy: #0b2d78;
    --royal: #0f3396;
    --gold: #e2b400;
    --gold-bright: #e8c300;
    --ink: #151a2a;
    --rule: #8a93b8;
    --ring: #1d4f8e;
    --shadow: rgba(20, 24, 50, 0.28);
  }
  * { margin: 0; padding: 0; box-sizing: border-box; }
  html, body { width: 834px; height: 1200px; overflow: hidden; }
  body { background: var(--page); position: relative; font-family: "Poppins", sans-serif; }

  .certificate {
    position: absolute; left: 37px; top: 306px; width: 760px; height: 588px;
    background: var(--paper); box-shadow: 0 4px 12px var(--shadow); overflow: hidden;
  }
  .office-backdrop {
    position: absolute; left: 120px; top: 230px; width: 640px; height: 320px;
    background: radial-gradient(ellipse at 55% 45%, rgba(150,155,165,0.22), rgba(200,203,210,0.10) 55%, rgba(255,255,255,0) 80%);
  }
  .decor { position: absolute; left: 0; top: 0; }

  .text-block { position: absolute; left: 214px; top: 0; right: 0; }
  .institute {
    position: absolute; top: 86px; left: 0; white-space: nowrap;
    font-family: "Montserrat", sans-serif; font-weight: 700; font-size: 14.5px;
    letter-spacing: 0.12em; color: var(--ink);
  }
  .title {
    position: absolute; top: 126px; left: -2px; white-space: nowrap;
    font-family: "Montserrat", sans-serif; font-weight: 900; font-size: 51px;
    letter-spacing: -0.5px; color: var(--navy); line-height: 1;
  }
  .subtitle {
    position: absolute; top: 183px; left: 0; white-space: nowrap;
    font-family: "Montserrat", sans-serif; font-weight: 900; font-size: 18.5px;
    letter-spacing: 0.36em; color: var(--gold-bright);
  }
  .presented {
    position: absolute; top: 276px; left: 0; line-height: 1.2;
    font-family: "Montserrat", sans-serif; font-weight: 600; font-size: 14.5px;
    letter-spacing: 0.14em; color: var(--ink);
  }
  .recipient {
    position: absolute; top: 318px; left: 6px; white-space: nowrap;
    font-family: "Mrs Saint Delafield", cursive; font-size: 54px; line-height: 56px; color: var(--ink);
  }
  .statement {
    position: absolute; top: 398px; left: -2px; width: 372px;
    font-size: 12.2px; line-height: 1.35; color: var(--ink);
  }
  .field {
    position: absolute; display: flex; align-items: baseline;
    font-family: "Poppins", sans-serif; font-size: 10.5px; letter-spacing: 0.05em;
    color: var(--gold); white-space: nowrap;
  }
  .field .rule { flex: 1; border-bottom: 1px dotted var(--rule); margin-left: 4px; height: 1px; }
  .field-course { top: 470px; left: -2px; width: 490px; }
  .field-date { top: 510px; left: -2px; width: 210px; }
  .field-signature { top: 510px; left: 217px; width: 271px; }
</style>
</head>
<body>
  <main class="certificate">
    <div class="office-backdrop" role="img" aria-label="Faint greyscale photo of a bright office with people at work"></div>

    <svg class="decor" width="760" height="588" viewBox="0 0 760 588" aria-hidden="true">
      <rect class="top-bar-stub" x="0" y="0" width="30" height="14" fill="var(--gold-bright)"/>
      <rect class="top-bar" x="189" y="0" width="555" height="14" fill="var(--gold-bright)"/>
      <rect class="gold-block" x="41" y="0" width="137" height="80" fill="var(--gold)"/>
      <rect class="ribbon-band" x="42" y="93" width="140" height="320" fill="var(--royal)"/>
      <polygon points="42,93 182,93 182,300 42,180" fill="var(--navy)" opacity="0.35"/>
      <text x="112" y="148" text-anchor="middle" font-family="Montserrat, sans-serif" font-weight="900" font-size="30" fill="#ffffff">GSEA</text>
      <g class="award-seal">
        <circle cx="114" cy="463" r="69" fill="var(--ring)"/>
        <circle cx="114" cy="463" r="57" fill="var(--gold)"/>
        <circle cx="114" cy="463" r="50" fill="#f4f4f6"/>
      </g>
    </svg>

    <section class="text-block">
      <p class="institute">GLOBAL SERVICE EXCELLENCE ACADEMY</p>
      <h1 class="title">CERTIFICATE</h1>
      <p class="subtitle">OF COMPLETION</p>
      <p class="presented">PRESENTED TO</p>
      <p class="recipient">Daniel Hartley</p>
      <p class="statement">Your participation is a testament to your commitment to learning and proffessional growth.</p>
      <div class="field field-course">EDUCATION COURSE<span class="rule"></span></div>
      <div class="field field-date">DATE JOINED<span class="rule"></span></div>
      <div class="field field-signature">SIGNATURE<span class="rule"></span></div>
    </section>
  </main>
</body>
</html>
```